Create a memorable Web Design for real estate branding

we are a Minnepolis brokerage and boutique housing specialist with over 27 years of experience in the Global furnished housing industry, servicing the Greater Los Angeles area. Specializing in “warm environments” we offer a customized approach to satisfying our guests and client’s needs by offering a wide array of options in highly desirable areas. Additionally, Lantern Dwelling Partners offers assistance and expertise to home buyers, sellers and investors.

Industry/Entity Type

Real Estate

Number of Pages Required

1 page

Font styles to use
Serif
Sans Serif
Decorative

```html
<!DOCTYPE html>
<html lang="en">
<head>
<meta charset="utf-8">
<title>Lantern Dwelling Partners</title>
<link href="https://fonts.googleapis.com/css2?family=Cinzel:wght@400;700&family=Mulish:wght@300;400;600&display=swap" rel="stylesheet">
<style>
:root{
  --green:#8dc63f;
  --teal:#0ea88a;
  --teal-dark:#0b8f76;
  --ink:#3d3d3d;
  --grey:#777;
  --rule:#e4e4e4;
  --footer:#383a42;
  --footer-deep:#2d2e34;
  --field:#2a2b31;
  --white:#fff;
}
*{box-sizing:border-box;margin:0;padding:0}
html,body{width:1200px;height:2715px;overflow:hidden;background:var(--white)}
body{position:relative;font-family:'Mulish',sans-serif;color:var(--ink)}
.serif{font-family:'Cinzel',serif}
.abs{position:absolute}

.site-header{position:absolute;left:0;top:0;width:1200px;height:101px;background:var(--white)}
.brand{position:absolute;left:132px;top:24px;font-family:'Cinzel',serif;font-weight:700;color:var(--teal);font-size:25px;line-height:1.15;letter-spacing:.5px}
.nav{position:absolute;left:509px;top:0;display:flex;height:101px}
.nav a{display:flex;align-items:center;padding:0 17px;font-family:'Cinzel',serif;font-size:14px;color:#555;text-decoration:none;height:101px}
.nav a.active{background:var(--green);color:var(--white);width:102px;justify-content:center}

.hero{position:absolute;left:0;top:101px;width:1200px;height:572px;
  background:linear-gradient(180deg,#5a5660 0%,#b98c5c 30%,#e6a659 48%,#8a6a55 62%,#4b4447 100%)}
.hero-title{position:absolute;left:0;width:1200px;top:270px;text-align:center;color:var(--white);font-family:'Cinzel',serif}
.hero-title .sub{font-size:31px;letter-spacing:1px;opacity:.9}
.hero-title .main{font-size:35px;font-weight:700;margin-top:6px;letter-spacing:1px}
.arrow{position:absolute;top:262px}

.welcome{position:absolute;left:0;top:673px;width:1200px;height:252px;background:var(--green);color:var(--white);text-align:center}
.welcome h1{font-family:'Cinzel',serif;font-weight:700;font-size:24px;margin-top:64px;letter-spacing:.5px}
.welcome p{width:1070px;margin:24px auto 0;font-size:14px;line-height:24px;font-weight:300}

.press{position:absolute;left:132px;top:955px;width:936px;height:50px;display:flex;justify-content:space-between;align-items:center}
.press span{display:block;height:22px;background:#8a8a8a;border-radius:3px;opacity:.75}
.press-shadow{position:absolute;left:132px;top:1022px;width:936px;height:14px;background:radial-gradient(ellipse at top,rgba(0,0,0,.12),transparent 70%)}

.section-title{position:absolute;left:132px;width:936px;text-align:center;font-family:'Cinzel',serif;font-weight:700;color:var(--green);font-size:23px}
.section-title::after{content:"";display:block;margin-top:16px;height:1px;background:var(--rule)}

.spec{position:absolute;top:1151px;width:288px}
.spec .photo{height:153px;position:relative}
.spec .tag{position:absolute;left:50%;top:50%;transform:translate(-50%,-50%);background:var(--teal);color:var(--white);font-family:'Cinzel',serif;font-weight:700;font-size:22px;padding:7px 20px;text-align:center;line-height:1.2;white-space:nowrap}
.spec p{margin-top:18px;font-size:14px;line-height:24px;color:var(--grey)}

.project{position:absolute;top:1575px;width:288px;height:398px;background:var(--teal)}
.project .photo{height:197px}
.project .head{display:flex;justify-content:space-between;align-items:center;padding:14px 12px 10px 20px;border-bottom:3px solid var(--green);margin:0 10px 0 0}
.project h3{font-family:'Cinzel',serif;font-weight:700;color:var(--white);font-size:23px}
.project .btn{background:var(--white);color:var(--teal-dark);font-family:'Cinzel',serif;font-size:11px;font-weight:700;padding:6px 10px}
.project p{padding:16px 20px 0;color:var(--white);font-size:14px;line-height:24px}

.testimonials{position:absolute;left:0;top:2020px;width:1200px;height:410px;background:linear-gradient(90deg,#4a4a4a,#6a6a6a 60%,#5a5a5a)}
.testimonials h2{position:absolute;left:0;width:1200px;top:70px;text-align:center;font-family:'Cinzel',serif;font-weight:700;color:var(--green);font-size:23px}
.quote{position:absolute;left:430px;top:188px;width:650px;color:var(--white);font-size:14px;line-height:24px}
.dots{position:absolute;left:430px;top:318px;display:flex;gap:12px}
.dots i{width:8px;height:8px;border-radius:50%;background:var(--white)}
.dots i.on{background:var(--green)}

.site-footer{position:absolute;left:0;top:2430px;width:1200px;height:225px;background:var(--footer);color:#ddd}
.foot-brand{position:absolute;left:132px;top:40px;font-family:'Cinzel',serif;font-weight:700;color:var(--teal);font-size:25px;line-height:1.15}
.foot-col{position:absolute;top:40px;font-size:11px;line-height:19px}
.foot-col h4{font-family:'Cinzel',serif;color:var(--green);font-size:14px;font-weight:700;margin-bottom:12px}
.field{width:226px;height:21px;background:var(--field);border:1px solid #44464e;font-size:10px;color:#777;padding:3px 8px;margin-bottom:5px}
.field.msg{height:48px}
.send{display:inline-block;background:var(--teal);color:var(--white);font-size:10px;padding:4px 20px;margin-top:3px}

.bottom-bar{position:absolute;left:0;top:2655px;width:1200px;height:60px;background:var(--footer-deep);color:#bbb;font-size:10px}
.bottom-bar .copy{position:absolute;left:132px;top:24px}
.social{position:absolute;left:1024px;top:22px;display:flex;gap:12px}
.social i{width:14px;height:14px;border-radius:50%;background:#ddd}
</style>
</head>
<body>

<header class="site-header">
  <div class="brand">Lantern Dwelling<br>Partners</div>
  <nav class="nav">
    <a class="active" href="#">Home</a>
    <a href="#">About Us</a>
    <a href="#">Services</a>
    <a href="#">Properties</a>
    <a href="#">Contact Us</a>
  </nav>
</header>

<section class="hero" role="img" aria-label="City skyline at sunset with a warm golden sky">
  <svg class="arrow" style="left:82px" width="22" height="40" viewBox="0 0 22 40"><path d="M18 4 4 20l14 16" fill="none" stroke="#fff" stroke-width="4"/></svg>
  <svg class="arrow" style="left:1096px" width="22" height="40" viewBox="0 0 22 40"><path d="M4 4l14 16L4 36" fill="none" stroke="#fff" stroke-width="4"/></svg>
  <div class="hero-title">
    <div class="sub">Specializing in</div>
    <div class="main">“Warm Environments”</div>
  </div>
</section>

<section class="welcome">
  <h1>Welcome to Lantern Dwelling Partners</h1>
  <p>Lorem ipsum dolor sit amet, consectetur adipiscing elit, sed do eiusmod tempor incididunt ut labore et dolore magna aliqua. Ut enim ad minim veniam, quis nostrud exercitation ullamco laboris nisi ut aliquip ex ea commodo consequat. Duis aute irure dolor in reprehenderit in voluptate velit esse cillum dolore eu fugiat nulla pariatur.</p>
</section>

<div class="press" aria-label="Press features">
  <span style="width:128px"></span>
  <span style="width:84px"></span>
  <span style="width:52px;height:36px;border-radius:50%"></span>
  <span style="width:166px"></span>
  <span style="width:142px"></span>
  <span style="width:194px"></span>
</div>
<div class="press-shadow"></div>

<h2 class="section-title" style="top:1062px">We Specialize In</h2>

<article class="spec" style="left:132px">
  <div class="photo" role="img" aria-label="Hand holding house keys over a desk" style="background:linear-gradient(135deg,#c9b9a4,#8d7a68)"><div class="tag">Real Estate</div></div>
  <p>Lorem ipsum dolor sit amet, consectetur adipiscing elit, sed do eiusmod tempor incididunt ut labore et dolore magna aliqua. Ut enim ad minim veniam</p>
</article>
<article class="spec" style="left:456px">
  <div class="photo" role="img" aria-label="Agent standing at a front door" style="background:linear-gradient(135deg,#d6d8dc,#6f8fb8)"><div class="tag">Brokerage</div></div>
  <p>Lorem ipsum dolor sit amet, consectetur adipiscing elit, sed do eiusmod tempor incididunt ut labore et dolore magna aliqua. Ut enim ad minim veniam</p>
</article>
<article class="spec" style="left:781px">
  <div class="photo" role="img" aria-label="Small green house model held in hands" style="background:linear-gradient(135deg,#d9ef9a,#5fb040)"><div class="tag">Boutique<br>Housing</div></div>
  <p>Lorem ipsum dolor sit amet, consectetur adipiscing elit, sed do eiusmod tempor incididunt ut labore et dolore magna aliquaUt enim ad minim veniam</p>
</article>

<h2 class="section-title" style="top:1487px">Our Projects</h2>

<article class="project" style="left:132px">
  <div class="photo" role="img" aria-label="White suburban house with a garden" style="background:linear-gradient(180deg,#cfe0ee,#e8e8e4 45%,#5f8a3a)"></div>
  <div class="head"><h3>Project 1</h3><span class="btn">View Details</span></div>
  <p>At vero eos et accusamus et iusto odio dignissimos ducimus qui blanditiis praesentium voluptatum deleniti atque corrupti</p>
</article>
<article class="project" style="left:457px">
  <div class="photo" role="img" aria-label="Modern house with a pool at dusk" style="background:linear-gradient(180deg,#3a4a6a,#a0704a 55%,#3c8fa8)"></div>
  <div class="head"><h3>Project 2</h3><span class="btn">View Details</span></div>
  <p>At vero eos et accusamus et iusto odio dignissimos ducimus qui blanditiis praesentium voluptatum deleniti atque corrupti</p>
</article>
<article class="project" style="left:781px">
  <div class="photo" role="img" aria-label="Blue craftsman house among tall trees" style="background:linear-gradient(180deg,#cfe0ee,#4a6f58 45%,#6d8f4a)"></div>
  <div class="head"><h3>Project 3</h3><span class="btn">View Details</span></div>
  <p>At vero eos et accusamus et iusto odio dignissimos ducimus qui blanditiis praesentium voluptatum deleniti atque corrupti</p>
</article>

<section class="testimonials" role="img" aria-label="Family portrait in front of a house, shown in greyscale">
  <h2>Testimonials</h2>
  <svg class="abs" style="left:200px;top:130px" width="146" height="170" viewBox="0 0 146 170">
    <polygon points="73,3 143,43 143,127 73,167 3,127 3,43" fill="var(--teal)"/>
    <polygon points="73,12 135,48 135,122 73,158 11,122 11,48" fill="#fff"/>
    <polygon points="73,18 129,51 129,119 73,152 17,119 17,51" fill="#9a9a9a" role="img" aria-label="Client portrait"/>
  </svg>
  <p class="quote">At vero eos et accusamus et iusto odio dignissimos ducimus qui blanditiis praesentium voluptatum deleniti atque corrupti quos dolores et quas molestias excepturi sint occaecati cupiditate non provident, similique sunt in culpa qui officia deserunt mollitia animi, id est laborum et dolorum fuga.</p>
  <div class="dots"><i class="on"></i><i></i><i></i><i></i></div>
</section>

<footer class="site-footer">
  <div class="foot-brand">Lantern Dwelling<br>Partners</div>
  <div class="foot-col" style="left:430px">
    <h4>Quick Links</h4>
    Home<br>About Us<br>Services<br>Properties<br>Contact Us
  </div>
  <div class="foot-col" style="left:576px">
    <h4>Contact Info</h4>
    Lantern Front Office<br>Harbor Lane 42<br>55401 Minneapolis | USA<br><br>Telephone: +1 612 555 0148<br>E-mail: hello@lanterndwelling.example
  </div>
  <div class="foot-col" style="left:806px">
    <h4>Contact Us</h4>
    <div class="field">Name</div>
    <div class="field">E-mail</div>
    <div class="field msg">Message</div>
    <span class="send">SEND</span>
  </div>
</footer>

<div class="bottom-bar">
  <div class="copy">© 2016 Company Name | All Rights Reserved</div>
  <div class="social"><i></i><i></i></div>
</div>

</body>
</html>
```